Emergency Management Consulting Needs a Website

Need to develop a website for an Emergency Management Consulting business. This website needs to be user friendly and resemble disaster preparedness, response, recovery, and mitigation. It must allow for me to make changes to it myself by adding pages, content and pictures. Looking for an advanced page to the website that allows monitoring of social media sites, hashtags, and keywords. Must have pictures of disasters on the site. Must try to integrate the logo colors, not excessive.

Reason: Did not receive anything sufficient to what I am looking for.

Industry/Entity Type

Government

Coding

Coded - Design and coding required

Number of Pages Required

5+ page

Requirements
Must have
• Logo, advanced social media monitoring page, allow for edits myself (content, pages, graphics) this must be a CMS of some sort, use logo color scheme (not excessively), must be professional looking, connect with Plivex Domain, find a hosting site, SEO, no "long" designs, minimize "dead" space, no social media feeds, no newsletter stuff.
• Menu items: Home, About Us, Services, Situation Monitor, Work With Us, Contact Us (hopefully these could be editable if I need to later)
• When you make a submission, please send me a message on which CMS you are using. Thank you.
Nice to have
• Examples of websites:
• https://www.qrt.vic.gov.au/
• http://www.larkenmoss.example/
• http://www.tulpaxo.example/
• http://vonmirelconsulting.example/
• http://www.calvornet.example/services/emergency-management
• https://zuq.example/
• http://www.vestimora.example/Responsibility/Sustainable-Development/HSE/Crisis-and-Emergency-Management/

```html
<!DOCTYPE html>
<html lang="en">
<head>
<meta charset="utf-8">
<title>Calder Fork Emergency Management</title>
<link href="https://fonts.googleapis.com/css2?family=Montserrat:wght@700&family=Open+Sans:wght@400;600;700&family=Teko:wght@400;500&display=swap" rel="stylesheet">
<style>
:root{
  --blue:#1f6cc0;
  --blue-soft:#5b8fc8;
  --orange:#e3781b;
  --dark:#2b2b2b;
  --darker:#1f1f1f;
  --ink:#333;
  --muted:#666;
  --white:#fff;
  --line:#d8d8d8;
  --nav-accent:#d43a3a;
}
*{margin:0;padding:0;box-sizing:border-box}
html,body{width:730px;height:1200px;overflow:hidden;background:var(--white)}
body{font-family:"Open Sans",Arial,sans-serif;color:var(--ink);position:relative}
.site-header{position:absolute;top:0;left:0;width:730px;height:58px;background:var(--white)}
.brand{position:absolute;left:60px;top:19px;display:flex;align-items:center;gap:8px}
.brand-dot{width:22px;height:22px;border-radius:50%;background:var(--blue)}
.brand-name{font-family:"Open Sans",Arial,sans-serif;font-weight:700;font-size:16px;color:#3a3f47;letter-spacing:.5px}
.main-nav{position:absolute;left:309px;top:0;display:flex;height:58px}
.main-nav a{display:block;font-size:8.5px;color:#333;text-decoration:none;line-height:12px;padding:32px 8px 0;height:56px}
.main-nav a.active{border-bottom:2px solid var(--nav-accent)}
.hero{position:absolute;top:58px;left:0;width:730px;height:317px;overflow:hidden}
.hero-photo{position:absolute;inset:0;background:linear-gradient(170deg,#6f8296 0%,#8d98a3 35%,#56606b 65%,#2f3d4e 100%)}
.hero-shade{position:absolute;inset:0;background:rgba(20,30,45,.25)}
.hero-band{position:absolute;left:0;top:0}
.hero-copy{position:absolute;left:332px;top:110px;width:398px;color:var(--white);white-space:nowrap;overflow:hidden}
.hero-copy h1{font-family:"Montserrat",Arial,sans-serif;font-size:23px;line-height:28px;font-weight:700;white-space:normal;width:360px}
.hero-copy p{font-size:7.6px;line-height:17px;margin-top:4px}
.btn{display:inline-block;text-decoration:none;font-weight:700;color:var(--white);text-align:center}
.btn-learn{position:absolute;left:337px;top:214px;width:113px;height:28px;line-height:28px;background:var(--blue-soft);font-size:8px;border-radius:1px}
.services{position:absolute;top:375px;left:0;width:730px;height:395px}
.section-title{position:absolute;top:30px;left:0;width:730px;text-align:center}
.section-title h2{font-family:"Teko",sans-serif;font-weight:400;font-size:38px;line-height:40px;color:#222;display:inline-block}
.title-rule{position:absolute;top:46px;height:1px;background:linear-gradient(90deg,transparent,var(--line))}
.title-rule.left{left:186px;width:118px}
.title-rule.right{left:443px;width:125px;background:linear-gradient(90deg,var(--line),transparent)}
.services .lead{position:absolute;top:80px;width:730px;text-align:center;font-size:7.5px;color:var(--muted)}
.case{position:absolute;top:127px;width:157px;height:164px;overflow:hidden}
.case-text{background:var(--blue);color:var(--white);text-align:center;padding:34px 16px 0}
.case-text h3{font-size:7.8px;font-weight:700;line-height:14px;letter-spacing:.2px}
.case-text p{font-size:7.3px;line-height:12.5px;margin-top:4px}
.case-photo{position:absolute;inset:0}
.case-label{position:absolute;left:0;bottom:0;width:157px;height:46px;background:linear-gradient(transparent,rgba(0,0,0,.55));color:var(--white);font-family:"Teko",sans-serif;font-size:22px;text-align:center;line-height:56px;letter-spacing:.5px}
.btn-cases{position:absolute;left:295px;top:315px;width:144px;height:28px;line-height:28px;background:var(--blue-soft);font-size:7.5px;border-radius:2px}
.about-band{position:absolute;top:770px;left:0;width:730px;height:202px;overflow:hidden}
.about-photo{position:absolute;inset:0;background:linear-gradient(135deg,#2a6fc0 0%,#3b7fc9 50%,#2766b5 100%)}
.about-band h2{position:absolute;top:46px;width:730px;text-align:center;font-family:"Teko",sans-serif;font-weight:400;font-size:22px;color:var(--white)}
.about-rule{position:absolute;left:250px;top:77px;width:238px;height:1px;background:rgba(255,255,255,.45)}
.about-band p{position:absolute;top:98px;left:100px;width:530px;text-align:center;font-size:7.7px;line-height:13.5px;color:var(--white)}
.btn-details{position:absolute;left:297px;top:148px;width:136px;height:27px;line-height:27px;background:var(--orange);font-size:8px;font-weight:600;border-radius:1px;display:flex;align-items:center;justify-content:center;gap:6px}
.site-footer{position:absolute;top:972px;left:0;width:730px;height:196px;background:var(--dark);color:var(--white)}
.footer-brand{position:absolute;left:66px;top:38px;display:flex;align-items:center;gap:8px}
.footer-brand .brand-dot{background:#888}
.footer-brand .brand-name{color:#d0d0d0}
.footer-about{position:absolute;left:69px;top:74px;width:190px;font-size:7.3px;line-height:12.4px}
.footer-col h4{font-family:"Teko",sans-serif;font-weight:400;font-size:16px;color:var(--orange)}
.blog{position:absolute;left:283px;top:30px;width:180px;font-size:7.3px;line-height:12.4px}
.blog h4{margin-bottom:4px}
.blog .date{color:var(--orange);font-size:6.5px;margin-top:2px}
.blog .more{color:var(--orange);font-size:6.5px;margin-top:4px;display:block;text-decoration:none}
.contact{position:absolute;left:512px;top:28px;width:200px;font-size:7.6px;line-height:10.5px}
.contact h4{margin-bottom:8px}
.contact-row{display:flex;gap:5px;margin-bottom:8px}
.contact-row svg{flex:none;margin-top:1px}
.contact-row b{font-weight:700;margin-right:3px}
.social{display:flex;gap:8px;margin-top:4px}
.social span{width:20px;height:20px;border-radius:50%;background:#8a8a8a}
.copyright{position:absolute;top:1168px;left:0;width:730px;height:32px;background:var(--darker);color:#aaa;font-size:7.5px;text-align:center;line-height:28px;font-family:Arial,sans-serif}
</style>
</head>
<body>
<header class="site-header">
  <div class="brand"><span class="brand-dot"></span><span class="brand-name">CALDER FORK</span></div>
  <nav class="main-nav">
    <a class="active" href="#">Home</a><a href="#">About Us</a><a href="#">Services</a><a href="#">Situation Monitor</a><a href="#">Work With Us</a><a href="#">Contact Us</a>
  </nav>
</header>

<section class="hero">
  <div class="hero-photo" role="img" aria-label="Photo of a cruise ship in harbour with black smoke rising from a fire"></div>
  <div class="hero-shade"></div>
  <svg class="hero-band" width="300" height="317" viewBox="0 0 300 317"><polygon points="150,0 220,0 80,160 230,317 160,317 10,160" fill="#1f6cc0" opacity=".55"/></svg>
  <div class="hero-copy">
    <h1>CALDER FORK EMERGENCY MANAGEMENT</h1>
    <p>We strive for a perfect delivery and promise to be there for anything you may need, every step of the way.<br>Click here to find out more about Freight Management and how we do it.</p>
  </div>
  <a class="btn btn-learn" href="#">LEARN MORE</a>
</section>

<section class="services">
  <span class="title-rule left"></span><span class="title-rule right"></span>
  <div class="section-title"><h2>Our Sevices</h2></div>
  <p class="lead">Lorem Ipsum is simply dummy text of the printing and typesetting industry.</p>
  <article class="case case-text" style="left:98px">
    <h3>9/11 EXPEDITED PUBLIC<br>ASSISTANCE CLOSEOUT</h3>
    <p>Vonmirel was given six months to reengineer the NDRA closeout process dealing with approximately $5 billion in public assistance grants and an additional $2.4 billion in 9/11 associated costs.</p>
  </article>
  <article class="case" style="left:286px">
    <div class="case-photo" role="img" aria-label="Photo of a boat burning on the water with black smoke" style="background:linear-gradient(180deg,#d8d8d8 0%,#3a3a3a 45%,#c0502a 60%,#4e5a66 100%)"></div>
    <div class="case-label">WILMINGTON, NC</div>
  </article>
  <article class="case" style="left:471px">
    <div class="case-photo" role="img" aria-label="Photo of a cruise ship in a fjord between snowy mountains" style="background:linear-gradient(180deg,#3f7fcf 0%,#9aa7b4 30%,#5a5e58 55%,#2f5f8f 100%)"></div>
    <div class="case-label">WILMINGTON, NC</div>
  </article>
  <a class="btn btn-cases" href="#">SEE MORE CASE STUDIES</a>
</section>

<section class="about-band">
  <div class="about-photo" role="img" aria-label="Blue tinted photo of a harbour with ships and smoke"></div>
  <h2>Calder Fork Emergency Management</h2>
  <span class="about-rule"></span>
  <p>simply dummy text of the printing and typesetting industry. Lorem Ipsum has been the industry's standard dummy text ever since the 1500s, when an unknown printer took a galley of type and scrambled it to make a type specimen book.</p>
  <a class="btn btn-details" href="#"><svg width="9" height="9" viewBox="0 0 10 10"><path d="M5 1v8M3 3h4M1.5 6c0 2 2 3 3.5 3s3.5-1 3.5-3" stroke="#fff" stroke-width="1.3" fill="none"/><circle cx="5" cy="1.5" r="1" fill="#fff"/></svg>MORE DETAILS</a>
</section>

<footer class="site-footer">
  <div class="footer-brand"><span class="brand-dot"></span><span class="brand-name">CALDER FORK</span></div>
  <p class="footer-about">simply dummy text of the printing and typesetting industry. Lorem Ipsum has been the industry's standard dummy text ever since the 1500s, when an unknown printer took a galley of type and scrambled it to make a type specimen book.</p>
  <div class="footer-col blog">
    <h4>Calder Fork Blog</h4>
    <p>Posted by: Calder Fork<br>http://www.newsdeskwire.example/id/58213907/</p>
    <p class="date">5/4/2012</p>
    <p>And once workforce balance has been achieved, ignite its capacity with transformational team-building programs!</p>
    <a class="more" href="#">Read More...</a>
  </div>
  <div class="footer-col contact">
    <h4>Contact Us</h4>
    <div class="contact-row"><svg width="8" height="10" viewBox="0 0 8 10"><path d="M4 0a3.5 3.5 0 0 0-3.5 3.5C.5 6 4 10 4 10s3.5-4 3.5-6.5A3.5 3.5 0 0 0 4 0z" fill="#fff"/><circle cx="4" cy="3.5" r="1.3" fill="#2b2b2b"/></svg><span><b>Address*</b>2750 Harrow Ave<br>Lindale, CA 90512<br>United States</span></div>
    <div class="contact-row"><svg width="9" height="9" viewBox="0 0 10 10"><path d="M2 0l2 2.5-1 1.2c.6 1.3 1.7 2.4 3 3l1.2-1L10 8 8.5 10C4 9.5.5 6 0 1.5z" fill="#fff"/></svg><span><b>Phone:</b> +48 555 019 274</span></div>
    <div class="contact-row"><svg width="10" height="8" viewBox="0 0 10 8"><rect width="10" height="8" fill="#fff"/><path d="M0 0l5 4 5-4" stroke="#2b2b2b" fill="none"/></svg><span><b>E-mail:</b> info@calderfork.example</span></div>
    <div class="social"><span></span><span></span><span></span><span></span><span></span></div>
  </div>
</footer>
<div class="copyright">© Copyright 2016 Calder Fork Emercency Management. All Right Reserved.</div>
</body>
</html>
```